Corvane Business Cards

Front of business card will have logo, name, address, & telephone number. Back of card will have a list of services provided - Roads, Substation Pads, Temporary Pads, Site Pads, Land Leveling, Powerline Row Cleaning, Land Clearing, Gates, Fencing, Construction Entrances, Excavation, Trenching, Underground Utilities, Directional Boring, Pile Driving. We are a construction company that uses heavy equipment like bulldozers, motor graders/blades, dump trucks, backhoes, hydro axes, & skid loaders. We build roads, pads, & install electric utility lines & waterlines underground. This logo is new. The word "Construction" can be smaller as uploaded 2 example edited logos. We will be using this card design for many employees.
Target Market(s)
Industrial Electric Powerline, Wind Turbine, Solar Panel, & Water Utility companies.
Contact Information for Business Card
Name/Position - Dwayne Halster - Owner
Address: 4875 FM 309
Brannock, OK 73412
Phone number - (555) 482-5096

```html
<!DOCTYPE html>
<html lang="en">
<head>
<meta charset="utf-8">
<title>Corvane Business Cards</title>
<link rel="stylesheet" href="https://fonts.googleapis.com/css2?family=Arimo:wght@400;700&display=swap">
<style>
  :root {
    --stage: #efeceb;
    --maroon: #3a1019;
    --frost: #e6e1e1;
    --mark: #4a1a22;
    --mark-faint: #9a8a8c;
    --ink-light: #ffffff;
  }
  * { margin: 0; padding: 0; box-sizing: border-box; }
  html, body { width: 1200px; height: 900px; overflow: hidden; }
  body {
    background: var(--stage);
    font-family: "Arimo", Arial, sans-serif;
    position: relative;
  }
  .card {
    position: absolute;
    width: 556px;
    height: 344px;
    display: flex;
    box-shadow: 0 6px 18px rgba(0,0,0,0.12);
  }
  .card--front { left: 238px; top: 62px; }
  .card--back { left: 458px; top: 518px; }

  .panel-dark {
    background: var(--maroon);
    color: var(--ink-light);
  }
  .panel-frost {
    background: var(--frost);
    display: flex;
    flex-direction: column;
    align-items: center;
    justify-content: center;
  }
  .card--front .panel-dark { width: 269px; padding: 101px 20px 0 40px; }
  .card--front .panel-frost { width: 287px; }
  .card--back .panel-frost { width: 275px; }
  .card--back .panel-dark { width: 281px; padding: 78px 0 0 30px; }

  .contact-name { font-size: 21px; font-weight: 700; line-height: 1; white-space: nowrap; }
  .contact-role { font-size: 15.5px; margin-top: 4px; }
  .contact-phone { font-size: 18px; font-weight: 700; margin-top: 17px; }
  .contact-address { font-size: 15px; line-height: 21px; margin-top: 14px; }

  .wordmark {
    font-weight: 700;
    color: var(--mark);
    text-align: center;
    line-height: 1;
  }
  .wordmark__name { font-size: 44px; letter-spacing: 1px; }
  .wordmark__sub { font-size: 20px; letter-spacing: 1.5px; margin-top: 14px; }
  .wordmark--faint { color: var(--mark-faint); }

  .services { list-style: none; font-size: 15.5px; line-height: 21px; }
</style>
</head>
<body>
  <section class="card card--front" aria-label="Business card front">
    <div class="panel-dark">
      <p class="contact-name">DWAYNE HALSTER</p>
      <p class="contact-role">Owner</p>
      <p class="contact-phone">P: (555) 482-5096</p>
      <p class="contact-address">4875 FM 309<br>Brannock, OK 73412</p>
    </div>
    <div class="panel-frost">
      <div class="wordmark">
        <p class="wordmark__name">CORVANE</p>
        <p class="wordmark__sub">CONSTRUCTION</p>
      </div>
    </div>
  </section>

  <section class="card card--back" aria-label="Business card back">
    <div class="panel-frost">
      <div class="wordmark wordmark--faint">
        <p class="wordmark__name">CORVANE</p>
        <p class="wordmark__sub">CONSTRUCTION</p>
      </div>
    </div>
    <div class="panel-dark">
      <ul class="services">
        <li>Roads | Substation Pads</li>
        <li>Temporary Pads | Site Pads</li>
        <li>Land Leveling | Powerline</li>
        <li>Row Cleaning | Land Clearing</li>
        <li>Gates | Fencing</li>
        <li>Construction Entrances</li>
        <li>Excavation | Trenching</li>
        <li>Underground Utilities</li>
        <li>Directional Boring | Pile Driving.</li>
      </ul>
    </div>
  </section>
</body>
</html>
```